Redesign of the UI of a customer service platform

To improve the user experience of our customers, we need a new design for our agent interface of our customer service platform (velorant.com).
The focus will be on the dashboard and the inbox screens (see attached) along with the common UI elements (Buttons, menu, fonts, forms...)
We want a simple and distinctive design

Target Market(s)

Worldwide

Industry/Entity Type

It Service

Number of Pages Required

3 page

Font styles to use
Sans Serif

Requirements
Must have
• New Onboarding page: this is a new page that is shown to user the first time they login to the platform. This will replace the current onboarding screen (setup SMS, Setup widget...etc)
• Dashboard page: to access important information and activate services (see screenshot from current site)
• Inbox page: to manage all the interactions with customers. (see screenshot from current site)
• UI elements (buttons, menus, forms, tables, fonts, color palette)

```html
<!DOCTYPE html>
<html lang="en">
<head>
<meta charset="utf-8">
<title>Velorant – Onboarding</title>
<link href="https://fonts.googleapis.com/css2?family=Open+Sans:wght@400;600&display=swap" rel="stylesheet">
<style>
:root{
  --ink:#555;
  --ink-soft:#666;
  --ink-dark:#333;
  --line:#dcdcdc;
  --nav-active:#f1f1f1;
  --card-bg:#f2f2f2;
  --accent-red:#e86a62;
  --accent-blue:#3a8fc0;
  --badge-green:#2ecc8a;
  --badge-blue:#6ab0e4;
  --play-blue:#1aa6d8;
  --footer-bg:#f5f5f5;
}
*{box-sizing:border-box;margin:0;padding:0}
html,body{width:1200px;height:861px;overflow:hidden;background:#fff;font-family:"Open Sans",Arial,sans-serif;color:var(--ink)}
.app{position:relative;width:1200px;height:861px}
.topbar{position:absolute;left:0;top:0;width:1200px;height:62px;border-bottom:1px solid var(--line)}
.brand{position:absolute;left:0;top:0;width:86px;height:61px;display:flex;align-items:center;justify-content:center;font-size:13px;font-weight:600;color:var(--ink-dark)}
.nav{position:absolute;left:86px;top:0;display:flex;height:61px}
.nav-item{position:relative;width:99.5px;height:61px;border-right:1px solid var(--line);display:flex;flex-direction:column;align-items:center;justify-content:flex-end;padding-bottom:10px;font-size:10.5px;color:var(--ink);text-transform:uppercase}
.nav-item:first-child{border-left:1px solid var(--line)}
.nav-item.is-active{background:var(--nav-active)}
.nav-item svg{margin-bottom:9px}
.nav-badge{position:absolute;top:24px;right:7px;width:22px;height:22px;border-radius:50%;color:#fff;font-size:11px;display:flex;align-items:center;justify-content:center}
.nav-badge.green{background:var(--badge-green)}
.nav-badge.blue{background:var(--badge-blue)}
.user{position:absolute;left:1044px;top:9px;display:flex;align-items:center}
.avatar{position:relative;width:46px;height:46px;border-radius:50%;border:2px solid var(--badge-green);background:radial-gradient(circle at 50% 45%,#c99a80,#6b4a3a 70%,#3d2c24)}
.avatar::after{content:"";position:absolute;left:-3px;top:-2px;width:10px;height:10px;border-radius:50%;background:var(--badge-green)}
.user-name{margin-left:9px;font-size:11px;color:var(--ink);text-transform:uppercase}
.video-frame{position:absolute;left:285px;top:126px;width:631px;height:373px;border:1px solid var(--line);background:#f4f4f4;padding:8px}
.video-still{position:absolute;left:8px;top:8px;width:615px;height:356px;background:linear-gradient(110deg,#e9edee 0%,#dfe4e4 30%,#f4f4f2 48%,#e6eaea 70%,#cfd8da 100%)}
.play-big{position:absolute;left:360px;top:177px;width:78px;height:78px;border-radius:50%;background:var(--accent-red);box-shadow:0 3px 8px rgba(0,0,0,.25);display:flex;align-items:center;justify-content:center}
.player-bar{position:absolute;left:14px;top:336px;width:603px;height:24px;display:flex;align-items:center}
.player-btn{width:47px;height:28px;background:#3d4448;display:flex;align-items:center;justify-content:center;border-radius:2px}
.player-track{position:relative;margin-left:6px;flex:1;height:22px;background:#3d4448;border-radius:2px;display:flex;align-items:center;padding:0 8px}
.player-time{position:absolute;left:-6px;top:-10px;font-size:8px;background:#fff;color:#333;padding:0 2px;font-family:monospace}
.player-line{flex:1;height:8px;border:1px solid #6a7377}
.player-vol{margin-left:6px;width:26px;height:8px;background:repeating-linear-gradient(90deg,var(--play-blue) 0 2px,transparent 2px 4px)}
.player-name{margin-left:24px;font-size:12px;font-weight:600;color:#fff}
.section-title{position:absolute;left:0;top:541px;width:1200px;text-align:center;font-size:27px;font-weight:400;color:var(--accent-blue)}
.addons{position:absolute;left:183px;top:615px;display:flex;gap:21.5px}
.addon{position:relative;width:150px;height:154px;background:var(--card-bg);border:1px solid var(--line);display:flex;flex-direction:column;align-items:center}
.addon-icon{height:44px;margin-top:30px;display:flex;align-items:center;justify-content:center}
.addon-name{margin-top:10px;font-size:17px;font-weight:600;color:var(--ink-soft)}
.addon-link{margin-top:4px;font-size:13px;color:var(--ink-soft);display:flex;align-items:center;gap:6px}
.addon-check{position:absolute;left:7px;top:7px;width:24px;height:24px;border-radius:50%;background:var(--badge-green);display:flex;align-items:center;justify-content:center}
.footer{position:absolute;left:0;top:831px;width:1200px;height:30px;background:var(--footer-bg);border-top:1px solid var(--line);font-size:11px;color:var(--ink);display:flex;align-items:center;justify-content:center}
.footer-code{position:absolute;right:8px}
</style>
</head>
<body>
<div class="app">
  <header class="topbar">
    <div class="brand">Velorant</div>
    <nav class="nav">
      <div class="nav-item is-active"><svg width="14" height="11" viewBox="0 0 14 11"><rect x=".5" y=".5" width="13" height="10" fill="none" stroke="#666"/><path d="M.5.5 7 6l6.5-5.5" fill="none" stroke="#666"/></svg>Inbox<span class="nav-badge green">4</span></div>
      <div class="nav-item"><svg width="11" height="13" viewBox="0 0 11 13"><path d="M.5.5h7l3 3v9h-10z" fill="none" stroke="#666"/><path d="M3 6h5M3 8h5M3 10h5" stroke="#666"/></svg>Tasks<span class="nav-badge blue">4</span></div>
      <div class="nav-item"><svg width="12" height="12" viewBox="0 0 12 12"><circle cx="6" cy="3.5" r="3" fill="#666"/><path d="M1 12c0-4 2-5 5-5s5 1 5 5z" fill="#666"/></svg>Customers</div>
      <div class="nav-item"><svg width="14" height="13" viewBox="0 0 14 13"><path d="M13 .5 1 6l4 1.5 1 5 2-3.5 3 2z M5 7.5 13 .5" fill="none" stroke="#666"/></svg>Campaigns</div>
      <div class="nav-item"><svg width="15" height="11" viewBox="0 0 15 11"><rect x=".5" y=".5" width="14" height="10" fill="none" stroke="#666"/><rect x="1" y="3" width="13" height="2" fill="#666"/></svg>Payments</div>
      <div class="nav-item"><svg width="14" height="12" viewBox="0 0 14 12"><path d="M.5 0v11.5H14" fill="none" stroke="#666"/><path d="M3 10V6M5.5 10V3M8 10V5M10.5 10V2" stroke="#666" stroke-width="1.5"/></svg>Reports</div>
      <div class="nav-item"><svg width="12" height="12" viewBox="0 0 12 12"><circle cx="6" cy="6" r="4.5" fill="#666"/><circle cx="6" cy="6" r="1.6" fill="#fff"/><path d="M6 0v12M0 6h12M1.8 1.8l8.4 8.4M10.2 1.8l-8.4 8.4" stroke="#666" stroke-width="2"/></svg>Settings</div>
    </nav>
    <div class="user">
      <div class="avatar" role="img" aria-label="Agent profile photo"></div>
      <span class="user-name">Marcus Delane</span>
    </div>
  </header>

  <section class="video-frame">
    <div class="video-still" role="img" aria-label="Video still of a smiling businessman at a desk in a bright office"></div>
    <div class="play-big"><svg width="30" height="34" viewBox="0 0 30 34"><path d="M2 0 30 17 2 34z" fill="#fff"/></svg></div>
    <div class="player-bar">
      <div class="player-btn"><svg width="12" height="14" viewBox="0 0 12 14"><path d="M0 0 12 7 0 14z" fill="#fff"/></svg></div>
      <div class="player-track"><span class="player-time">02:12</span><div class="player-line"></div><div class="player-vol"></div><span class="player-name">Clipora</span></div>
    </div>
  </section>

  <h1 class="section-title">Select your Add-ons</h1>

  <section class="addons">
    <div class="addon">
      <span class="addon-check"><svg width="12" height="10" viewBox="0 0 12 10"><path d="M1 5l3.5 3.5L11 1.5" fill="none" stroke="#fff" stroke-width="2.2"/></svg></span>
      <div class="addon-icon"><svg width="44" height="38" viewBox="0 0 44 38"><rect x="0" y="0" width="44" height="30" rx="3" fill="var(--accent-red)"/><rect x="4" y="4" width="36" height="20" fill="#fff"/><rect x="18" y="30" width="8" height="5" fill="var(--accent-red)"/><rect x="12" y="35" width="20" height="3" fill="var(--accent-red)"/></svg></div>
      <div class="addon-name">Widget</div>
      <div class="addon-link"><svg width="12" height="12" viewBox="0 0 12 12"><circle cx="6" cy="6" r="6" fill="var(--play-blue)"/><path d="M4.5 3.5 8.5 6l-4 2.5z" fill="#fff"/></svg>Watch video</div>
    </div>
    <div class="addon">
      <div class="addon-icon"><svg width="34" height="34" viewBox="0 0 34 34"><circle cx="17" cy="17" r="16" fill="var(--accent-red)"/></svg></div>
      <div class="addon-name">Chatline</div>
      <div class="addon-link"><svg width="12" height="12" viewBox="0 0 12 12"><circle cx="6" cy="6" r="6" fill="var(--play-blue)"/><path d="M4.5 3.5 8.5 6l-4 2.5z" fill="#fff"/></svg>Watch video</div>
    </div>
    <div class="addon">
      <div class="addon-icon"><svg width="48" height="38" viewBox="0 0 48 38"><path d="M18 3C9 3 3 8 3 14c0 4 2 7 5 9l-2 6 7-4c2 .5 3 .5 5 .5 9 0 15-5 15-11.5S27 3 18 3z" fill="none" stroke="var(--accent-red)" stroke-width="3.5"/><path d="M37 13c5 2 8 5 8 9 0 3-1.5 5-4 7l2 6-7-4c-2 .5-3 .5-5 .5-5 0-9-2-11-5" fill="none" stroke="var(--accent-red)" stroke-width="3.5"/></svg></div>
      <div class="addon-name">Sms</div>
      <div class="addon-link"><svg width="12" height="12" viewBox="0 0 12 12"><circle cx="6" cy="6" r="6" fill="var(--play-blue)"/><path d="M4.5 3.5 8.5 6l-4 2.5z" fill="#fff"/></svg>Watch video</div>
    </div>
    <div class="addon">
      <div class="addon-icon"><svg width="34" height="34" viewBox="0 0 34 34"><rect x="1" y="1" width="32" height="32" fill="var(--accent-red)"/></svg></div>
      <div class="addon-name">Relaygram</div>
      <div class="addon-link"><svg width="12" height="12" viewBox="0 0 12 12"><circle cx="6" cy="6" r="6" fill="var(--play-blue)"/><path d="M4.5 3.5 8.5 6l-4 2.5z" fill="#fff"/></svg>Watch video</div>
    </div>
    <div class="addon">
      <div class="addon-icon"><svg width="26" height="42" viewBox="0 0 26 42"><path d="M13 0v42" stroke="var(--accent-red)" stroke-width="3.5"/><path d="M22 10c-2-3-5-4-9-4-5 0-8 2.5-8 6 0 8 17 5 17 14 0 4-4 7-9 7-4 0-8-2-10-5" fill="none" stroke="var(--accent-red)" stroke-width="4"/></svg></div>
      <div class="addon-name">Payment</div>
      <div class="addon-link"><svg width="12" height="12" viewBox="0 0 12 12"><circle cx="6" cy="6" r="6" fill="var(--play-blue)"/><path d="M4.5 3.5 8.5 6l-4 2.5z" fill="#fff"/></svg>Watch video</div>
    </div>
  </section>

  <footer class="footer">Copyrights 2017. Velorant. All rights reserved.<span class="footer-code">C8</span></footer>
</div>
</body>
</html>
```